Bloomtandem.com Greeting cards

We need a total of 15 digital greeting cards. in the following categories of life milestones. 3 of each to start.

1. Bar Mitzvah and Bat Mitzvah
2. Sweet 16
3. Babies Birth
4. Anniversary
5. Birthday

```html
<!DOCTYPE html>
<html lang="en">
<head>
<meta charset="utf-8">
<title>Happy Anniversary Card</title>
<link rel="stylesheet" href="https://fonts.googleapis.com/css2?family=Didact+Gothic&family=Great+Vibes&display=swap">
<style>
  :root {
    --pattern-cream: #eef0cf;
    --pattern-green: #dfe4b4;
    --paper: #ffffff;
    --frame: #ffffff;
    --photo-light: #7a4535;
    --photo-dark: #4a2419;
    --greeting-red: #e0262b;
  }
  html, body {
    margin: 0;
    padding: 0;
    width: 1200px;
    height: 900px;
    overflow: hidden;
    background: var(--paper);
  }
  .card {
    position: relative;
    width: 1200px;
    height: 900px;
    overflow: hidden;
  }
  .card__damask {
    position: absolute;
    inset: 0;
    background: linear-gradient(135deg, var(--pattern-cream) 0%, var(--pattern-green) 100%);
  }
  .card__photo-frame {
    position: absolute;
    left: 69px;
    top: 73px;
    width: 510px;
    height: 725px;
    background: var(--frame);
    box-shadow: 0 1px 3px rgba(0,0,0,0.12);
  }
  .card__photo {
    position: absolute;
    left: 16px;
    top: 15px;
    width: 477px;
    height: 695px;
    background: linear-gradient(180deg, var(--photo-light) 0%, var(--photo-dark) 100%);
  }
  .card__panel {
    position: absolute;
    left: 621px;
    top: 17px;
    width: 558px;
    height: 866px;
    background: var(--paper);
  }
  .greeting {
    position: absolute;
    inset: 0;
    color: var(--greeting-red);
    font-family: "Didact Gothic", "Century Gothic", sans-serif;
    font-size: 27px;
    line-height: 1;
  }
  .greeting__line {
    position: absolute;
    margin: 0;
    white-space: nowrap;
    line-height: 27px;
  }
  .greeting__initial {
    font-family: "Great Vibes", cursive;
    font-size: 46px;
    line-height: 0;
  }
  .greeting__line--wishes { left: 98px; top: 232px; }
  .greeting__line--love { left: 125px; top: 271px; }
  .greeting__line--better { left: 69px; top: 330px; }
  .greeting__line--treasure { left: 85px; top: 376px; }
  .greeting__line--wishing { left: 187px; top: 419px; }
  .greeting__script {
    position: absolute;
    margin: 0;
    white-space: nowrap;
    font-family: "Great Vibes", cursive;
    font-weight: 400;
    line-height: 1;
  }
  .greeting__script--happy { left: 69px; top: 462px; font-size: 50px; }
  .greeting__script--anniversary { left: 185px; top: 497px; font-size: 66px; }
</style>
</head>
<body>
  <main class="card">
    <div class="card__damask" role="img" aria-label="Pale green and cream damask floral pattern background"></div>

    <div class="card__photo-frame">
      <div class="card__photo" role="img" aria-label="Photo of a four-tier anniversary cake with white fondant, red hearts and a chocolate polka-dot base"></div>
    </div>

    <section class="card__panel">
      <div class="greeting">
        <p class="greeting__line greeting__line--wishes"><span class="greeting__initial">W</span>e send anniversary wishes...,</p>
        <p class="greeting__line greeting__line--love">for joyful happiness and love....</p>
        <p class="greeting__line greeting__line--better">May each year keep getting better,</p>
        <p class="greeting__line greeting__line--treasure">with memories to treasure...</p>
        <p class="greeting__line greeting__line--wishing">Wishing you a</p>
        <h1 class="greeting__script greeting__script--happy">Happy</h1>
        <p class="greeting__script greeting__script--anniversary">Anniversary!</p>
      </div>
    </section>
  </main>
</body>
</html>
```